Harbor Ridge Painting Epoxy Flyer

We need a promotional flyer for a new epoxy floor coatings division of our painting company. We do epoxy garage floor coatings and paver sealing. It needs to be based on and very similar to the attached flyer. The garage floor picture needs to look more realistic, and the before and after pavers pictures should look less shiny but still a good contrast. Include attached logo

```html
<!DOCTYPE html>
<html lang="en">
<head>
<meta charset="utf-8">
<title>Harbor Ridge Painting – Garage &amp; Driveway Flyer</title>
<link rel="stylesheet" href="https://fonts.googleapis.com/css2?family=Anton&family=Oswald:wght@500;600&family=Poppins:wght@500;600&family=Montserrat:wght@600;700&display=swap">
<style>
  :root {
    --backdrop: #c0c0c0;
    --paper: #ffffff;
    --ink: #000000;
    --green: #4ea720;
    --blue: #2289d8;
    --orange: #d9731c;
    --photo-before-a: #8a867c;
    --photo-before-b: #5e5c57;
    --photo-after-a: #c9cacb;
    --photo-after-b: #9fa2a5;
  }
  * { box-sizing: border-box; margin: 0; padding: 0; }
  html, body { width: 904px; height: 1200px; overflow: hidden; }
  body { background: var(--backdrop); position: relative; }

  .flyer {
    position: absolute; left: 137px; top: 127px;
    width: 630px; height: 946px;
    background: var(--paper); overflow: hidden;
  }
  .flyer-backdrop { position: absolute; inset: 0; }

  .brand { position: absolute; left: 24px; top: 68px; display: flex; align-items: center; gap: 10px; }
  .brand-dot { width: 44px; height: 44px; border-radius: 50%; background: var(--green); }
  .brand-name {
    font: 700 14px/1.25 "Montserrat", sans-serif; color: var(--ink);
    letter-spacing: 0.5px; text-transform: uppercase;
  }

  .headline { position: absolute; right: 29px; top: 34px; text-align: right; color: var(--ink); }
  .headline-main { font: 400 63px/1 "Anton", sans-serif; }
  .headline-sub { font: 400 44px/1 "Anton", sans-serif; margin-top: 4px; }
  .tagline { font: 700 21px/1.25 "Montserrat", sans-serif; margin-top: 8px; }

  .before-after { position: absolute; left: 34px; top: 177px; }
  .ba-label { font: 400 23px "Anton", sans-serif; fill: #fff; }

  .trust-list { position: absolute; left: 411px; top: 325px; list-style: none; }
  .trust-item { display: flex; align-items: center; gap: 10px; height: 50px; margin-bottom: 11px; }
  .trust-icon { width: 48px; height: 48px; flex: none; }
  .trust-text { font: 600 19px/1.1 "Oswald", sans-serif; color: #fff; }

  .service {
    position: absolute; top: 575px; width: 273px; height: 159px;
    border: 1.5px solid transparent; border-radius: 12px;
    background: linear-gradient(var(--ink), var(--ink)) padding-box,
                linear-gradient(180deg, var(--blue), var(--orange)) border-box;
  }
  .service--epoxy { left: 33px; }
  .service--pavers { left: 324px; }
  .service-title {
    position: absolute; left: 17px; top: -17px; width: 238px; height: 34px;
    border-radius: 17px; text-align: center;
    font: 600 23px/34px "Oswald", sans-serif; color: #fff;
  }
  .service--epoxy .service-title { background: var(--blue); }
  .service--pavers .service-title { background: var(--green); }
  .service-list { list-style: none; position: absolute; left: 33px; top: 27px; width: 235px; }
  .service--pavers .service-list { left: 19px; width: 250px; }
  .service-list li {
    position: relative; padding-left: 18px; margin-bottom: 11px;
    font: 500 13.5px/1.2 "Poppins", sans-serif; color: #fff;
  }
  .service-list li::before {
    content: "✓"; position: absolute; left: 0; top: 3px;
    width: 11px; height: 11px; border-radius: 50%;
    font: 700 8px/11px sans-serif; text-align: center; color: #fff;
  }
  .service--epoxy li::before { background: var(--blue); }
  .service--pavers li::before { background: var(--green); }

  .promise {
    position: absolute; left: 0; width: 100%; top: 748px; text-align: center;
    font: 500 26px/1.2 "Oswald", sans-serif; color: #fff;
  }
  .cta {
    position: absolute; left: 0; width: 100%; top: 784px; text-align: center;
    font: 400 53px/1.1 "Anton", sans-serif; color: #fff;
  }

  .contact-band {
    position: absolute; left: 0; bottom: 0; width: 100%; height: 92px;
    background: var(--green); color: #fff; text-align: center;
  }
  .contact-phone {
    display: flex; align-items: center; justify-content: center; gap: 12px;
    padding-top: 12px; padding-right: 20px;
  }
  .phone-icon { width: 44px; height: 44px; }
  .phone-number { font: 600 48px/1 "Poppins", sans-serif; letter-spacing: 0.5px; }
  .contact-note { font: 600 20px/1 "Poppins", sans-serif; margin-top: 5px; }
</style>
</head>
<body>
  <main class="flyer">
    <svg class="flyer-backdrop" width="630" height="946" viewBox="0 0 630 946" aria-hidden="true">
      <path d="M0,330 C110,390 260,230 400,190 C500,160 580,180 630,285 L630,946 L0,946 Z" fill="var(--blue)"/>
      <path d="M0,366 C120,430 280,290 410,245 C500,215 570,230 630,329 L630,946 L0,946 Z" fill="var(--ink)"/>
    </svg>

    <div class="brand">
      <span class="brand-dot"></span>
      <span class="brand-name">Harbor Ridge<br>Painting</span>
    </div>

    <header class="headline">
      <h1 class="headline-main">Upgrade Your</h1>
      <p class="headline-sub">Garage &amp; Driveway</p>
      <p class="tagline">FROM WORN-OUT<br>TO LIKE NEW</p>
    </header>

    <svg class="before-after" width="364" height="364" viewBox="0 0 364 364">
      <defs>
        <clipPath id="ba-clip"><circle cx="182" cy="182" r="176"/></clipPath>
        <linearGradient id="before-tone" x1="0" y1="0" x2="0" y2="1">
          <stop offset="0" stop-color="var(--photo-before-a)"/>
          <stop offset="1" stop-color="var(--photo-before-b)"/>
        </linearGradient>
        <linearGradient id="after-tone" x1="0" y1="0" x2="0" y2="1">
          <stop offset="0" stop-color="var(--photo-after-a)"/>
          <stop offset="1" stop-color="var(--photo-after-b)"/>
        </linearGradient>
      </defs>
      <circle cx="182" cy="182" r="182" fill="#fff"/>
      <g clip-path="url(#ba-clip)">
        <rect x="0" y="68" width="182" height="296" fill="url(#before-tone)" role="img" aria-label="Photo of a weathered, stained paver walkway before sealing"/>
        <rect x="182" y="68" width="182" height="296" fill="url(#after-tone)" role="img" aria-label="Photo of the same paver walkway cleaned and sealed"/>
        <rect x="0" y="0" width="364" height="68" fill="var(--green)"/>
        <rect x="180" y="0" width="3" height="364" fill="#fff"/>
      </g>
      <text class="ba-label" x="128" y="52" text-anchor="middle">Before</text>
      <text class="ba-label" x="239" y="52" text-anchor="middle">After</text>
    </svg>

    <ul class="trust-list">
      <li class="trust-item">
        <svg class="trust-icon" viewBox="0 0 48 48" aria-hidden="true">
          <circle cx="24" cy="24" r="22" fill="none" stroke="var(--blue)" stroke-width="1.2"/>
          <circle cx="24" cy="21" r="10" fill="var(--green)"/>
          <path d="M19 21l4 4 7-8" fill="none" stroke="#fff" stroke-width="2.4" stroke-linecap="round" stroke-linejoin="round"/>
          <path d="M18 30l-3 7 5-2 2 4 2-7M30 30l3 7-5-2-2 4-2-7" fill="var(--orange)"/>
        </svg>
        <span class="trust-text">Licensed &amp;<br>Insured</span>
      </li>
      <li class="trust-item">
        <svg class="trust-icon" viewBox="0 0 48 48" aria-hidden="true">
          <circle cx="24" cy="24" r="22" fill="none" stroke="var(--green)" stroke-width="1.2"/>
          <path d="M24 11l11 4v8c0 7-5 12-11 14-6-2-11-7-11-14v-8z" fill="var(--blue)"/>
          <path d="M19 23l4 4 7-7" fill="none" stroke="#fff" stroke-width="2.4" stroke-linecap="round" stroke-linejoin="round"/>
        </svg>
        <span class="trust-text">Family-Owned<br>Local Business</span>
      </li>
      <li class="trust-item">
        <svg class="trust-icon" viewBox="0 0 48 48" aria-hidden="true">
          <circle cx="24" cy="24" r="22" fill="none" stroke="var(--orange)" stroke-width="1.2"/>
          <ellipse cx="24" cy="35" rx="10" ry="3.5" fill="none" stroke="var(--orange)" stroke-width="2"/>
          <path d="M24 35c-6-7-9-11-9-16a9 9 0 0 1 18 0c0 5-3 9-9 16z" fill="var(--green)"/>
          <circle cx="24" cy="19" r="3.5" fill="#fff"/>
        </svg>
        <span class="trust-text">Serving Prescott &amp;<br>Surrounding Areas</span>
      </li>
    </ul>

    <section class="service service--epoxy">
      <h2 class="service-title">Epoxy Floor Coatings</h2>
      <ul class="service-list">
        <li>Durable, long-lasting finish</li>
        <li>Slip-resistant texture</li>
        <li>Covers cracks &amp;<br>imperfections</li>
        <li>Easy to clean &amp; maintain</li>
      </ul>
    </section>

    <section class="service service--pavers">
      <h2 class="service-title">Paver Sealing</h2>
      <ul class="service-list">
        <li>Restores color &amp; enhances<br>appearance</li>
        <li>Protects from sun fading</li>
        <li>Helps prevent weeds &amp; sand loss</li>
        <li>Easier to clean &amp; maintain</li>
      </ul>
    </section>

    <p class="promise">Practical upgrades that protect and improve your home</p>
    <p class="cta">CALL FOR A FREE ESTIMATE</p>

    <footer class="contact-band">
      <div class="contact-phone">
        <svg class="phone-icon" viewBox="0 0 44 44" aria-hidden="true">
          <circle cx="22" cy="22" r="22" fill="#fff"/>
          <path d="M15 12c1-1 2-1 3 0l3 4c.6 1 .4 2-.4 2.7l-1.6 1.3c1 2.5 3 4.5 5.5 5.5l1.3-1.6c.7-.8 1.7-1 2.7-.4l4 3c1 1 1 2 0 3l-2 2c-1.5 1.5-4 1.5-7 0-5-2.5-9-6.5-11.5-11.5-1.5-3-1.5-5.5 0-7z" fill="var(--green)"/>
          <path d="M25 12a8 8 0 0 1 7 7M25 16a4 4 0 0 1 3 3" fill="none" stroke="var(--blue)" stroke-width="1.8" stroke-linecap="round"/>
        </svg>
        <span class="phone-number">928-555-0147</span>
      </div>
      <p class="contact-note">Fast, professional service you can trust</p>
    </footer>
  </main>
</body>
</html>
```